Robotic Physical Therapy office needs a Grand Opening Flyer

We need a Grand Opening flyer design for a robotic physical therapy office named Kinetic Harbor Wellness. We would like it to have a clean, classy, upscale feeling that gives potential clients a V.I.P. feeling. We would like to use the colors black, gray, and yellow (logo will be uploaded).

Event: Thursday, June 1st, 2023 from 12pm-6pm
location: 58274 Pellham Ave, Alder Springs, OR 48519

Industry/Entity Type

Physical therapy

Font styles to use
Script

Colors

Designer to choose colors to be used in the design.

Requirements
Nice to have
• More of a vip feel for the invite

```html
<!DOCTYPE html>
<html lang="en">
<head>
<meta charset="utf-8">
<title>Kinetic Harbor Wellness – Grand Opening</title>
<link rel="stylesheet" href="https://fonts.googleapis.com/css2?family=Krona+One&family=Lexend:wght@300;400;500&family=Lato:wght@700&display=swap">
<style>
  :root {
    --page-bg: #f4f4f6;
    --flyer-top: #221d33;
    --flyer-bottom: #15121f;
    --yellow: #f5dc28;
    --white: #ffffff;
    --ring: #6e6596;
    --ring-fill: #1c1830;
    --muted: #d8d6e0;
  }
  html, body {
    margin: 0;
    width: 691px;
    height: 1200px;
    overflow: hidden;
    background: var(--page-bg);
  }
  .flyer {
    position: absolute;
    left: 35px;
    top: 200px;
    width: 620px;
    height: 800px;
    overflow: hidden;
    background: linear-gradient(180deg, var(--flyer-top) 0%, #1b1729 45%, var(--flyer-bottom) 100%);
    box-shadow: 0 8px 24px rgba(0,0,0,.18);
    font-family: "Lexend", sans-serif;
    color: var(--white);
  }
  .accent-line {
    position: absolute;
    height: 4px;
    z-index: 3;
  }
  .accent-line--top {
    top: 0; right: 0; width: 210px;
    background: linear-gradient(90deg, rgba(245,220,40,0), var(--yellow) 35%);
  }
  .accent-line--bottom {
    bottom: 6px; left: 0; width: 360px;
    background: linear-gradient(90deg, var(--yellow) 65%, rgba(245,220,40,0));
  }
  .brand {
    position: absolute;
    top: 76px; left: 0; right: 0;
    display: flex; justify-content: center; align-items: center; gap: 10px;
  }
  .brand__dot {
    width: 44px; height: 44px; border-radius: 50%;
    background: var(--white);
  }
  .brand__name {
    font-family: "Lato", sans-serif;
    font-weight: 700;
    color: var(--yellow);
    font-size: 24px;
    line-height: 1.05;
    text-transform: uppercase;
  }
  .headline {
    position: absolute; left: 0; right: 0; margin: 0;
    text-align: center;
    font-family: "Krona One", sans-serif;
    font-weight: 400;
    white-space: nowrap;
    line-height: 1;
    z-index: 2;
  }
  .headline--grand { top: 170px; font-size: 78px; color: var(--yellow); letter-spacing: 1px; }
  .headline--opening { top: 252px; font-size: 80px; color: var(--white); letter-spacing: -3px; }
  .photo-ring {
    position: absolute; left: 0; top: 0;
  }
  .photo-area {
    position: absolute;
    left: 290px; top: 345px;
    width: 330px; height: 435px;
    background: linear-gradient(160deg, rgba(190,190,196,.45) 0%, rgba(120,120,130,.35) 50%, rgba(60,60,72,.25) 100%);
    border-radius: 60px 0 0 40px;
  }
  .event-day {
    position: absolute; left: 66px; top: 360px;
    font-size: 34px; font-weight: 300; color: var(--yellow);
    margin: 0; letter-spacing: .5px;
  }
  .event-date {
    position: absolute; left: 66px; top: 410px;
    display: flex; align-items: flex-start;
  }
  .event-date__month {
    writing-mode: vertical-rl; transform: rotate(180deg);
    font-size: 16px; font-weight: 300; color: var(--white);
    border-left: 2px solid var(--yellow); border-right: 2px solid var(--yellow);
    padding: 0 2px; height: 66px; text-align: center; letter-spacing: 1px;
  }
  .event-date__num {
    font-family: "Krona One", sans-serif; font-size: 62px; line-height: 66px;
    margin-left: 10px;
  }
  .event-date__suffix {
    font-family: "Krona One", sans-serif; font-size: 30px; line-height: 1; margin-left: 4px; margin-top: 2px;
  }
  .event-year {
    position: absolute; left: 64px; top: 494px;
    width: 190px;
    font-size: 28px; font-weight: 300; color: var(--yellow); letter-spacing: 12px;
    border-top: 1px solid var(--yellow); border-bottom: 1px solid var(--yellow);
    padding: 2px 0 1px;
    border-image: linear-gradient(90deg, var(--yellow) 55%, rgba(245,220,40,0)) 1;
  }
  .info {
    position: absolute; left: 66px; margin: 0;
    font-size: 16px; font-weight: 300; line-height: 1.35;
  }
  .info--time { top: 574px; }
  .info--time strong { font-weight: 400; font-size: 16px; }
  .info--address { top: 664px; color: var(--muted); }
  .dots {
    position: absolute; left: 66px; height: 0;
    border-top: 2px dotted var(--muted);
  }
  .dots--time { top: 624px; width: 186px; }
  .dots--address { top: 716px; width: 195px; }
</style>
</head>
<body>
  <article class="flyer">
    <div class="accent-line accent-line--top"></div>

    <header class="brand">
      <span class="brand__dot"></span>
      <span class="brand__name">Kinetic Harbor<br>Wellness</span>
    </header>

    <svg class="photo-ring" width="620" height="800" viewBox="0 0 620 800" aria-hidden="true">
      <circle cx="434" cy="490" r="153" fill="var(--ring-fill)" stroke="var(--ring)" stroke-width="4"/>
    </svg>

    <div class="photo-area" role="img" aria-label="Photo of a client exercising on a robotic elliptical trainer"></div>

    <h1 class="headline headline--grand">GRAND</h1>
    <h2 class="headline headline--opening">OPENING</h2>

    <p class="event-day">THURSDAY</p>
    <div class="event-date">
      <span class="event-date__month">JUNE</span>
      <span class="event-date__num">1</span>
      <span class="event-date__suffix">ST</span>
    </div>
    <div class="event-year">2023</div>

    <p class="info info--time">from<br><strong>12pm-6pm</strong></p>
    <div class="dots dots--time"></div>

    <p class="info info--address">58274 Pellham Ave,<br>Alder Springs, OR 48519</p>
    <div class="dots dots--address"></div>

    <div class="accent-line accent-line--bottom"></div>
  </article>
</body>
</html>
```